Brightfield Ventures Inc. Letterhead

Creation of attractive and eye catching letterhead for a business start-up for the construction industry. Letterhead must relate to construction, but avoid standard hammer and tools in the design.

I forgot to add some details, sorry about that. Some pertinent info: Ph: 916-555-0187 brightfieldventures.example 448 Willowmere Ave, Ste 210 Folsom, CA 95999 info@brightfieldventures.example not sure if slogan should be in there" “Connecting construction professionals to create a purpose driven industry.” must be able to be used in word. Thanks!

```html
<!DOCTYPE html>
<html lang="en">
<head>
<meta charset="utf-8">
<title>Brightfield Ventures Inc. Letterhead</title>
<link href="https://fonts.googleapis.com/css2?family=Lato:wght@400;700&family=Yellowtail&display=swap" rel="stylesheet">
<style>
  :root {
    --navy: #1b1f4f;
    --red: #c4232b;
    --body: #4f4f4f;
    --ink: #222222;
    --paper: #ffffff;
  }
  * { margin: 0; padding: 0; box-sizing: border-box; }
  html, body { width: 883px; height: 1200px; overflow: hidden; background: var(--paper); }
  .letterhead {
    position: relative;
    width: 883px;
    height: 1200px;
    background: var(--paper);
    font-family: "Lato", sans-serif;
    overflow: hidden;
  }
  .brand-name {
    position: absolute;
    left: 65px;
    top: 66px;
    font-size: 25px;
    font-weight: 700;
    color: var(--navy);
    letter-spacing: 0.5px;
  }
  .contact-list {
    position: absolute;
    right: 62px;
    top: 51px;
    list-style: none;
    border-left: 1px solid #d9d9d9;
    padding-left: 8px;
  }
  .contact-list li {
    display: flex;
    align-items: center;
    gap: 5px;
    font-size: 13px;
    line-height: 19px;
    color: #555555;
  }
  .contact-list svg { width: 10px; height: 10px; flex: none; }
  .letter-body {
    position: absolute;
    left: 65px;
    top: 322px;
    width: 756px;
  }
  .salutation {
    font-size: 16px;
    font-weight: 700;
    color: var(--navy);
    margin-bottom: 18px;
  }
  .letter-body p.paragraph {
    font-size: 16px;
    line-height: 25.6px;
    color: var(--body);
    text-align: justify;
    margin-bottom: 20px;
  }
  .closing {
    margin-top: 22px;
    font-size: 19px;
    color: var(--ink);
  }
  .signature {
    font-family: "Yellowtail", cursive;
    font-size: 34px;
    color: var(--navy);
    margin-top: 2px;
  }
  .footer-wave {
    position: absolute;
    left: 0;
    top: 0;
    width: 883px;
    height: 1200px;
    pointer-events: none;
  }
  .footer-address {
    position: absolute;
    left: 65px;
    top: 1141px;
    font-size: 15px;
    line-height: 22px;
    color: #ffffff;
  }
</style>
</head>
<body>
<main class="letterhead">
  <header>
    <div class="brand-name">Brightfield Ventures Inc.</div>
    <ul class="contact-list">
      <li>
        <svg viewBox="0 0 10 10" aria-hidden="true"><circle cx="5" cy="5" r="4.3" fill="none" stroke="#c4232b" stroke-width="1.2"/><path d="M3.4 2.8 L4.4 3.8 L3.9 4.6 Q4.8 6 5.6 6.2 L6.3 5.7 L7.2 6.6 L6.4 7.4 Q4.2 7 2.7 3.6 Z" fill="#c4232b"/></svg>
        916-555-0187
      </li>
      <li>
        <svg viewBox="0 0 10 10" aria-hidden="true"><rect x="0.8" y="2.2" width="8.4" height="5.8" fill="#c4232b"/><path d="M0.8 2.4 L5 5.6 L9.2 2.4" fill="none" stroke="#fff" stroke-width="0.9"/></svg>
        info@brightfieldventures.example
      </li>
      <li>
        <svg viewBox="0 0 10 10" aria-hidden="true"><circle cx="5" cy="5" r="4.3" fill="#c4232b"/><path d="M0.8 5 H9.2 M5 0.7 V9.3 M5 0.7 Q2.4 5 5 9.3 M5 0.7 Q7.6 5 5 9.3" fill="none" stroke="#fff" stroke-width="0.7"/></svg>
        www.brightfieldventures.example
      </li>
    </ul>
  </header>

  <section class="letter-body">
    <p class="salutation">Dear Mr. Lorem,</p>
    <p class="paragraph">Lorem ipsum dolor sit amet, consectetuer adipiscing elit, sed diam nonummy nibh euismod tincidunt ut laoreet dolore magna aliquam erat volutpat. Ut wisi enim ad minim veniam, quis nostrud exerci tation ullamcorper suscipit lobortis nisl ut aliquip ex ea commodo consequat. Duis autem vel eum iriure dolor in hendiusto odio dignissim qui blandit praesent luptatum zzril delenit augue duis dolore te feugait nulla facilisi.</p>
    <p class="paragraph">Lorem ipsum dolor sit amet, consectetuer adipiscing elit, sed diam nonummy nibh euismod tincidunt ut laoreet dolore magna aliquam erat volutpat. Ut wisi enim ad minim veniam, quis nostrud exerci tation ullamcorper suscipit lobortis nisl ut aliquip ex ea commodo consequat. Duis autem vel eum iriure dolor in hendiusto odio dignissim qui blandit praesent luptatum zzril delenit augue duis dolore te feugait nulla facilisi.</p>
    <p class="paragraph">Lorem ipsum dolor sit amet, consectetuer adipiscing elit, sed diam nonummy nibh euismod tincidunt ut laoreet dolore magna aliquam erat volutpat. Ut wisi enim ad minim veniam, quis nostrud exerci tation ullamcorper suscipit lobortis nisl ut aliquip ex ea commodo consequat. Duis autem vel eum iriure dolor in hendiusto odio dignissim qui blandit praesent luptatum zzril delenit augue duis dolore te feugait nulla facilisi.</p>
    <p class="closing">Sincerely Your,</p>
    <p class="signature">Your Name</p>
  </section>

  <svg class="footer-wave" viewBox="0 0 883 1200" aria-hidden="true">
    <path d="M0 1093 C250 1066 420 1168 600 1158 C720 1151 820 1126 883 1113 L883 1200 L0 1200 Z" fill="var(--red)"/>
    <path d="M0 1103 C250 1080 420 1176 600 1166 C720 1159 820 1133 883 1120 L883 1200 L0 1200 Z" fill="var(--paper)"/>
    <path d="M0 1110 C250 1088 420 1182 600 1172 C720 1165 820 1140 883 1128 L883 1200 L0 1200 Z" fill="var(--navy)"/>
  </svg>

  <footer class="footer-address">
    Street Name, City Name<br>
    Zipcode-012345
  </footer>
</main>
</body>
</html>
```